Web design for new streaming audio service

We need a homepage design for a new streaming audio service. Our company is called Dunmoral, and we’re basically Vexlo for Audiobooks, Stand-Up Comedy, Lectures, Language Learning, etc. Essentially like Plumtrek for everything audio EXCEPT music.
You don’t have to code the homepage (Design Only), but it should include 3 different designs to work with 1) Web; 2) Phones; 3) Tablets.
Below is a link to a mockup of the web version which gives a good idea of what elements we want. This is just a mockup and we want you to improve it.
Once you download the mockup, please refer to the more detailed instructions below:
The following outlines the design project for the Dunmoral homepage. We have provided a rough mockup of the homepage layout that gives you a general idea of what we’re going for. There are a few elements that we are attached to, and many others where you have complete creative freedom to do whatever you think looks good.
The ZIP file includes the following:
* Mockup to see what we have in mind (dunmoral-homepage-mockup.jpg)
* Text used (dunmoral-homepage-text.txt)
* Raw image of actor (dunmoral-actor1.jpg)
* Raw images for samples (dunmoral-sample-[name].jpg)
Although we have only provided a mockup layout for the web version, we also need you to provide a mobile phone and a tablet version of the design also. It’s very possible the tablet version may be substantially similar to the web version, but the mobile phone version will likely be much different.
All of the raw files are included in the attached ZIP file. Please use our photographs and text as provided although cropping, sizing, etc. is flexible per the instructions below.
Display Requirements:
* Web Version - Minimum resolution 1024x768 (72 dpi) but should look good on 1920x1080 (72 dpi) - Page should be designed to scale to look acceptable in all resolutions in between.
* Phone Version - Minimum Zarno 4 - 640x960 (326 dpi) but should look good on Harlow Quasar T5 - 1920x1080 (441 dpi) - Page should be designed to scale to look acceptable in all resolutions and devices in between.
* Tablet Version - Minimum Bristly Ember QX 7” - 1280x800 (216 dpi) but should also look good on a Tavo Breeze - 2048x1536 (264 dpi) - Page should be designed to scale to look acceptable in all resolutions and devices in between.
Above the Fold - We want to make sure the Dunmoral logo, Member Login Link, Large Photo, Headline, Price, Button, and the first row of sample images are all “Above the fold”. As a general guideline, this means 600 pixels high on a 1024x768 72 dpi web screen. This requirement is less important on Phone versions.
Top Logo Bar - We want to retain the blue bar with the Dunmoral logo on the page, although we are open to a different size, shape and positioning if it greatly enhances the design. Please use the standard logo color, although you are welcome to use either the horizontal or vertical orientation of the logo based on your design.
Text color, font and size - Feel free to design the text in anyway you choose as long as the text is readable on the target platforms.
Buttons - Feel free to use any size, shape and colors for the buttons as long as they are obvious and clickable relative to the page. The only exception is the Chatterly button should follow the Chatterly color scheme and logo treatment (the mockup doesn’t seem 100% correct.)
Top Photograph - We want to retain the large photograph across the top of the screen although final shape and dimensions are flexible.
Size and shape of content samples (i.e. Audiobooks, Stand-Up Comedy, etc.) - Feel free to design the content samples in anyway you choose.
Three Sales Points (i.e. Listen on your Zarno…, All you can enjoy…, etc.) - The Three Sales Points are envisioned to each have a corresponding illustration which you should provide and have rights for. The placeholder is represented by a square next to the text. The color size and shape of these elements are flexible and can be designed in any way you choose.
Opt-in form - Feel free to design the opt-in form in anyway you choose as long as the text is readable and the interactivity is obvious on the target platforms.
Text links and copyright notice - Feel free to design the bottom of the page text links and copyright notice in anyway you choose.
Additional colors, graphic design elements, etc. - Feel free to use any additional colors, graphic design elements, etc. to support your design.
people who want to listen to audio through their mobile devices.
Graphic Design

```html
<!DOCTYPE html>
<html lang="en">
<head>
<meta charset="utf-8">
<title>Dunmoral — Unlimited listening</title>
<link rel="stylesheet" href="https://fonts.googleapis.com/css2?family=Open+Sans:ital,wght@0,400;0,600;0,700;1,400&display=swap">
<style>
:root{
  --brand-blue:#5aaed6;
  --deep-blue:#1f6f99;
  --headline-blue:#2a7fb0;
  --orange:#f7941d;
  --ink:#333;
  --muted:#999;
  --panel:#f4f4f4;
  --panel-dark:#ececec;
  --line:#dedede;
  --footer:#2f2f2f;
  --social:#3b5998;
}
*{box-sizing:border-box;margin:0;padding:0}
html,body{width:774px;height:1200px;overflow:hidden}
body{position:relative;font-family:"Open Sans",Arial,sans-serif;color:var(--ink);background:#fff}
.abs{position:absolute}
.topbar{left:0;top:12px;width:774px;height:53px;background:var(--brand-blue)}
.brand{left:57px;top:10px;display:flex;align-items:center;gap:8px;color:#fff;font-size:26px;font-weight:600;letter-spacing:-.5px;white-space:nowrap}
.brand-mark{width:20px;height:20px;border-radius:50%;background:#fff}
.login{right:57px;top:12px;width:101px;height:29px;background:var(--deep-blue);color:#fff;font-size:11.5px;font-weight:600;display:flex;align-items:center;justify-content:center;white-space:nowrap}
.hero{left:0;top:65px;width:774px;height:392px}
.hero-photo{position:absolute;inset:0;background:linear-gradient(90deg,#6b5a52 0%,#8a7568 30%,#c9bdb2 55%,#f2efeb 70%,#fbfaf8 100%)}
.hero-copy{left:474px;top:70px;width:280px}
.hero-copy h1{font-size:27px;line-height:31px;font-weight:600;color:var(--headline-blue);letter-spacing:-.5px;white-space:nowrap}
.price{margin-top:4px;font-size:15px;color:#333;white-space:nowrap}
.cta{margin-top:10px;background:var(--orange);color:#fff;font-size:12px;font-weight:600;width:165px;height:29px;display:flex;align-items:center;justify-content:center;white-space:nowrap}
.note{margin-top:12px;font-size:8px;color:#555;white-space:nowrap}
.samples{left:0;top:457px;width:774px;height:430px;background:var(--panel);border-top:2px solid #ddd}
.samples h2{position:absolute;top:22px;width:100%;text-align:center;font-size:16.5px;font-weight:400;color:#444;white-space:nowrap}
.tile{position:absolute;width:157px;height:150px}
.tile-comedy{background:#2a2624;color:#fff;text-align:center}
.tile-comedy h3{margin-top:32px;font-size:13px;font-weight:600;white-space:nowrap}
.tile-comedy p{margin-top:10px;font-size:8px;line-height:13px;color:#ddd}
.tile-comedy .search{width:27px;height:27px;border-radius:50%;background:#4aa9dc;margin:14px auto 0;display:flex;align-items:center;justify-content:center}
.points{left:57px;top:887px;width:660px;height:78px;background:#fff;border:1px solid var(--line);display:flex}
.point{flex:1;position:relative;padding:12px 12px;border-right:1px solid var(--line)}
.point:last-child{border-right:0}
.point h4{font-size:10px;font-weight:400;line-height:14px;color:#333;width:150px;white-space:nowrap}
.point h4.lead{color:var(--headline-blue)}
.point p{margin-top:4px;font-size:7.5px;line-height:11px;color:var(--muted);width:140px}
.point svg{position:absolute;right:14px;top:18px}
.signup{left:0;top:985px;width:774px;height:180px;background:var(--panel-dark)}
.signup h2{position:absolute;left:65px;top:26px;font-size:19px;font-weight:600;color:#333;width:200px;padding-bottom:6px;border-bottom:1px solid #ccc;white-space:nowrap}
.signup .lede{position:absolute;left:65px;top:70px;width:215px;font-size:10px;line-height:17px;color:#666}
.signup .lede b{display:block;margin-top:2px;color:#333;font-weight:600;white-space:nowrap}
.email{position:absolute;left:319px;top:72px;width:384px;height:29px;background:#fff;border:1px solid #ddd;font-size:9px;font-style:italic;color:#aaa;padding:8px 6px}
.btn-access{position:absolute;left:318px;top:123px;width:161px;height:30px;background:#7b7b7b;color:#fff;font-size:11px;font-weight:600;display:flex;align-items:center;justify-content:center;white-space:nowrap}
.or{position:absolute;left:490px;top:132px;font-size:9px;color:#888;white-space:nowrap}
.btn-social{position:absolute;left:542px;top:123px;width:162px;height:30px;background:var(--social);color:#fff;font-size:10px;font-weight:600;display:flex;align-items:center;white-space:nowrap}
.btn-social .sq{flex:none;width:26px;height:30px;border-right:1px solid rgba(255,255,255,.25);display:flex;align-items:center;justify-content:center;margin-right:8px}
.btn-social .sq i{width:8px;height:8px;background:#fff;display:block}
.footer{left:0;top:1165px;width:774px;height:35px;background:var(--footer);color:#bbb;font-size:8px;white-space:nowrap}
.footer nav{position:absolute;left:57px;top:13px}
.footer nav span{margin:0 4px}
.footer .copy{position:absolute;right:57px;top:13px}
</style>
</head>
<body>
<div class="abs topbar">
  <div class="abs brand"><span class="brand-mark"></span>Dunmoral</div>
  <div class="abs login">MEMBER LOGIN</div>
</div>

<section class="abs hero">
  <div class="hero-photo" role="img" aria-label="Smiling young man wearing headphones, looking at his phone"></div>
  <div class="abs hero-copy">
    <h1>Unlimited listening.<br>Wherever you are.</h1>
    <div class="price">Only $9.99 per month</div>
    <div class="cta">START YOUR FREE TRAIL</div>
    <div class="note">*Credit Card Not Required</div>
  </div>
</section>

<section class="abs samples">
  <h2>A sample of what you can listen to on dunmoral</h2>
  <div class="tile" style="left:57px;top:78px;background:linear-gradient(#3a3a3a,#1a1a1a)" role="img" aria-label="Noir audiobook cover"></div>
  <div class="tile tile-comedy" style="left:224px;top:78px">
    <h3>Stand-Up Comedy</h3>
    <p>Nasrsae ertyao<br>lasoertasea mereatur suisqure.</p>
    <div class="search"><svg width="11" height="11" viewBox="0 0 11 11"><circle cx="4.5" cy="4.5" r="3.2" fill="none" stroke="#fff" stroke-width="1.6"/><line x1="7" y1="7" x2="10" y2="10" stroke="#fff" stroke-width="1.8"/></svg></div>
  </div>
  <div class="tile" style="left:392px;top:78px;background:linear-gradient(#1a2a4a 0 14%,#1aa0e0 14%,#0b7fc4)" role="img" aria-label="French language course cover"></div>
  <div class="tile" style="left:560px;top:78px;background:linear-gradient(#3a3a3a,#6a6a5a 70%,#5a9a4a)" role="img" aria-label="Biography audiobook cover"></div>
  <div class="tile" style="left:57px;top:239px;background:linear-gradient(#c04ac8,#7a2a8a)" role="img" aria-label="Total relaxation audio cover"></div>
  <div class="tile" style="left:224px;top:239px;background:linear-gradient(90deg,#5a2a10,#a06030 50%,#2a2a4a)" role="img" aria-label="Wealth building lecture cover"></div>
  <div class="tile" style="left:392px;top:239px;background:linear-gradient(#c03a2a,#8a5a3a 60%,#6a6a6a)" role="img" aria-label="Pop star biography cover"></div>
  <div class="tile" style="left:560px;top:239px;background:linear-gradient(#4ab0e0,#2a8ac8)" role="img" aria-label="Elliptical workout coaching cover"></div>
</section>

<section class="abs points">
  <div class="point">
    <h4 class="lead">Listen on your Zarno, Tavo<br>or Orbix device</h4>
    <p>Lorem ipsum dolor sit amet conse-ctetur adipiscing elit..</p>
    <svg width="48" height="36" viewBox="0 0 48 36"><rect x="2" y="3" width="40" height="30" rx="4" fill="none" stroke="#9cc9e3" stroke-width="2.5"/><rect x="33" y="12" width="12" height="22" rx="2" fill="#fff" stroke="#9cc9e3" stroke-width="2.5"/></svg>
  </div>
  <div class="point">
    <h4>All you can enjoy for one low<br>monthly price.</h4>
    <p>Lorem ipsum dolor sit amet consecte-tur adipiscing elit..</p>
    <svg width="40" height="44" viewBox="0 0 40 44"><circle cx="20" cy="20" r="16" fill="none" stroke="#bbb" stroke-width="3"/><rect x="16" y="36" width="8" height="6" fill="#bbb"/><text x="20" y="27" text-anchor="middle" font-family="Open Sans,sans-serif" font-weight="700" font-size="20" fill="#bbb">$</text></svg>
  </div>
  <div class="point">
    <h4>No obligation<br>Cancel any time.</h4>
    <p>Lorem ipsum dolor sit amet consecte-tur adipiscing elit..</p>
    <svg width="38" height="36" viewBox="0 0 38 36"><path d="M4 4 L34 32 M34 4 L4 32" stroke="#c4c4c4" stroke-width="5" stroke-linecap="round"/></svg>
  </div>
</section>

<section class="abs signup">
  <h2>Start Your Free Trail</h2>
  <div class="lede">You will get instant &amp; unlimited access to all the material on Dunmoral for 14 days. There is no obligation &amp; you can cancel at any time.<b>Credit card Not Required For Free Trail</b></div>
  <div class="email">Enter your email address...</div>
  <div class="btn-access">Get Instant Access</div>
  <div class="or">— OR —</div>
  <div class="btn-social"><span class="sq"><i></i></span>Sign Up Using Chatterly</div>
</section>

<footer class="abs footer">
  <nav>About<span>|</span>Help<span>|</span>Contact Us<span>|</span>Member Login<span>|</span>Privacy Policy<span>|</span>Terms Of Services</nav>
  <div class="copy">Copyrights © 2014 Dunmoral LLC - All Rights Reserved</div>
</footer>
</body>
</html>
```